Harlow Mechanical Contractors needs a Website

Create basic website for commercial plumbing and mechanical contractor; to include pictures of works in progress and completed works, description of all services offered and geographical locations and licenses

Target Market(s)

General Contractors, Real Estate Developers, Construction Companies

Industry/Entity Type

Construction

Coding

Coded - Design and coding required

Number of Pages Required

5+ page

• See logo attached to project

Colors
0392cd

```html
<!DOCTYPE html>
<html lang="en">
<head>
<meta charset="utf-8">
<title>Harlow Mechanical Contractors</title>
<link href="https://fonts.googleapis.com/css2?family=Open+Sans:wght@400;600;700&display=swap" rel="stylesheet">
<style>
:root{
  --brand:#0392cd;
  --navy:#1b4e7a;
  --ink:#333333;
  --muted:#7a7a7a;
  --band:#eef0f4;
  --footer:#3c3c3c;
  --footer-text:#d6d6d6;
  --white:#ffffff;
}
*{margin:0;padding:0;box-sizing:border-box}
html,body{width:1100px;height:1200px;overflow:hidden;background:var(--white)}
body{font-family:"Open Sans",Arial,sans-serif;color:var(--ink);position:relative}
.wrap{width:858px;margin:0 auto;position:relative}

.site-header{height:123px;position:relative}
.brand{position:absolute;left:0;top:26px;display:flex;align-items:center;gap:10px}
.brand-mark{width:44px;height:44px;border-radius:50%;background:var(--navy)}
.brand-name{font-size:15px;font-weight:700;color:var(--navy);line-height:1.15;width:140px;text-transform:uppercase}
.contact{position:absolute;right:0;top:28px;display:flex;align-items:center;gap:6px}
.contact-text{text-align:right}
.contact-email{font-size:11.5px;color:#555;display:block}
.contact-phone{font-size:15.5px;color:var(--navy);display:block;margin-top:1px}
.phone-badge{width:28px;height:28px;border-radius:50%;background:var(--navy);display:flex;align-items:center;justify-content:center}
.main-nav{position:absolute;right:0;top:88px;display:flex;gap:28px;font-size:11.5px}
.main-nav a{color:#555;text-decoration:none}
.main-nav a.active{color:var(--brand)}

.hero{height:439px;position:relative;background:linear-gradient(120deg,#c9c2bd 0%,#b8323a 35%,#d8303a 55%,#a7a3a0 75%,#c83a3e 100%)}
.hero-arrow{position:absolute;top:206px;width:22px;height:28px;background:rgba(90,90,90,.45);display:flex;align-items:center;justify-content:center}
.hero-arrow.prev{left:0}
.hero-arrow.next{right:0}

.welcome{text-align:center;padding-top:40px}
.welcome h1{font-size:31px;font-weight:400;color:var(--brand);line-height:1.2}
.welcome h2{font-size:15.5px;font-weight:400;color:var(--ink);margin-top:6px}
.welcome p{font-size:10.3px;line-height:17.6px;color:var(--muted);margin-top:8px}

.sectors{margin-top:27px;height:73px;background:var(--band);display:flex;align-items:center;padding:0 19px}
.sectors-lead{font-size:14.5px;color:var(--ink);width:157px}
.sector{display:flex;align-items:center;gap:13px;margin-right:48px}
.sector:last-child{margin-right:0}
.sector-icon{width:49px;height:49px;border-radius:50%;background:var(--brand);display:flex;align-items:center;justify-content:center}
.sector-name{font-size:18.5px;font-weight:600;color:var(--brand)}

.projects{margin-top:38px}
.projects-head{display:flex;justify-content:space-between;align-items:center}
.projects-head h3{font-size:21.5px;font-weight:400;color:var(--brand)}
.pager{display:flex;gap:1px}
.pager span{width:13px;height:15px;background:#6a6a6a;display:flex;align-items:center;justify-content:center}
.pager span:first-child{border-radius:8px 0 0 8px}
.pager span:last-child{border-radius:0 8px 8px 0}
.project-grid{display:flex;justify-content:space-between;margin-top:14px}
.project{width:200px;text-align:center}
.project-photo{height:135px}
.project-photo.pipes-trench{background:linear-gradient(160deg,#b89c7c,#4d4f55 55%,#c7ad8b)}
.project-photo.pipe-stack{background:linear-gradient(135deg,#5a5a5c,#1f1f21 60%,#8a8a8c)}
.project-photo.site-crew{background:linear-gradient(180deg,#9aa0a6,#7d7f78 55%,#a99a8a)}
.project-photo.timber-frame{background:linear-gradient(180deg,#4c7fc3 0%,#8fb2dc 40%,#c9a677 65%,#a8a39c 100%)}
.project-caption{font-size:10.5px;color:var(--muted);margin-top:12px}

.site-footer{position:absolute;left:0;right:0;bottom:0;height:74px;background:var(--footer)}
.footer-nav{position:absolute;left:0;top:20px;font-size:9.8px;color:var(--footer-text)}
.footer-nav a{color:var(--footer-text);text-decoration:none}
.footer-nav .sep{margin:0 8px}
.copyright{position:absolute;left:0;top:41px;font-size:9.8px;color:var(--footer-text)}
.social{position:absolute;right:0;top:25px;display:flex;gap:6px}
.social span{width:24px;height:24px;border-radius:50%}
.social .one{background:#3b5a9a}
.social .two{background:#29a9e1}
</style>
</head>
<body>

<header class="site-header wrap">
  <div class="brand">
    <span class="brand-mark"></span>
    <span class="brand-name">Harlow Mechanical Contractors</span>
  </div>
  <div class="contact">
    <div class="contact-text">
      <span class="contact-email">info@harlowmechanical.com</span>
      <span class="contact-phone">555 210 4870</span>
    </div>
    <span class="phone-badge">
      <svg width="12" height="12" viewBox="0 0 24 24"><path fill="#fff" d="M6.6 10.8a15 15 0 0 0 6.6 6.6l2.2-2.2c.3-.3.7-.4 1-.2 1.1.4 2.3.6 3.6.6.6 0 1 .4 1 1V20c0 .6-.4 1-1 1A17 17 0 0 1 3 4c0-.6.4-1 1-1h3.5c.6 0 1 .4 1 1 0 1.3.2 2.5.6 3.6.1.3 0 .7-.2 1z"/></svg>
    </span>
  </div>
  <nav class="main-nav">
    <a class="active" href="#">Home</a>
    <a href="#">About Us</a>
    <a href="#">Services</a>
    <a href="#">Projects</a>
    <a href="#">Contact Us</a>
  </nav>
</header>

<section class="hero" role="img" aria-label="Close-up of stacked red-flanged industrial pipes on a job site">
  <span class="hero-arrow prev"><svg width="8" height="14" viewBox="0 0 8 14"><path d="M7 1 1 7l6 6" stroke="#fff" fill="none" stroke-width="1.3"/></svg></span>
  <span class="hero-arrow next"><svg width="8" height="14" viewBox="0 0 8 14"><path d="m1 1 6 6-6 6" stroke="#fff" fill="none" stroke-width="1.3"/></svg></span>
</section>

<main class="wrap">
  <section class="welcome">
    <h1>Welcome</h1>
    <h2>We are Commercial Plumbing and Mechanical Contractor</h2>
    <p>Nullam accumsan purus vel tempus viverra. Mauris suscipit felis id nunc elementum varius. Praesent elementum nulla sit amet justo pellentesque scelerisque. Nam et tortor in ante iaculis porttitor in luctus mi. Vivamus gravida sem a pretium euismod. Nam lobortis, purus et fringilla tempus, risus eros dignissim diam, eget finibus sem risus sit amet eros. Vestibulum facilisis dolor at purus tincidunt porta. Nam fringilla nulla vel nisl condimentum, dapibus condimentum enim porta. Phasellus blandit quam a ipsum gravida dapibus. Cras sed augue tortor. Suspendisse elit ligula, iaculis dignissim justo eu, vestibulum venenatis elit.</p>
  </section>

  <section class="sectors">
    <span class="sectors-lead">We do projects for...</span>
    <div class="sector">
      <span class="sector-icon"><svg width="14" height="16" viewBox="0 0 14 16"><rect x="2" y="1" width="10" height="14" fill="none" stroke="#fff" stroke-width="1.5"/><g fill="#fff"><rect x="4.5" y="4" width="2" height="2"/><rect x="7.5" y="4" width="2" height="2"/><rect x="4.5" y="8" width="2" height="2"/><rect x="7.5" y="8" width="2" height="2"/><rect x="6" y="12" width="2" height="3"/></g></svg></span>
      <span class="sector-name">Large Offices</span>
    </div>
    <div class="sector">
      <span class="sector-icon"><svg width="24" height="12" viewBox="0 0 24 12"><g fill="#fff"><path d="M0 6 5 2l5 4v6H0z"/><path d="M7 5l5-5 5 5v7H7z"/><path d="M14 6l5-4 5 4v6H14z"/></g></svg></span>
      <span class="sector-name">Condominiums</span>
    </div>
    <div class="sector">
      <span class="sector-icon"><svg width="16" height="14" viewBox="0 0 16 14"><path fill="#fff" d="M1 14V6l4 2V6l4 2V6l4 2V1h2v13z"/></svg></span>
      <span class="sector-name">Industrial Projects</span>
    </div>
  </section>

  <section class="projects">
    <div class="projects-head">
      <h3>Our Projects</h3>
      <div class="pager">
        <span><svg width="6" height="8" viewBox="0 0 6 8"><path d="M5 0v8L0 4z" fill="#fff"/></svg></span>
        <span><svg width="6" height="8" viewBox="0 0 6 8"><path d="M1 0v8l5-4z" fill="#fff"/></svg></span>
      </div>
    </div>
    <div class="project-grid">
      <figure class="project">
        <div class="project-photo pipes-trench" role="img" aria-label="Large pipeline laid in a sandy trench"></div>
        <figcaption class="project-caption">Mauris suscipit felis id nunc</figcaption>
      </figure>
      <figure class="project">
        <div class="project-photo pipe-stack" role="img" aria-label="Stack of steel pipe ends"></div>
        <figcaption class="project-caption">Mauris suscipit felis id nunc</figcaption>
      </figure>
      <figure class="project">
        <div class="project-photo site-crew" role="img" aria-label="Crew in safety vests on a street work site"></div>
        <figcaption class="project-caption">Mauris suscipit felis id nunc</figcaption>
      </figure>
      <figure class="project">
        <div class="project-photo timber-frame" role="img" aria-label="Timber-framed building under construction"></div>
        <figcaption class="project-caption">Mauris suscipit felis id nunc</figcaption>
      </figure>
    </div>
  </section>
</main>

<footer class="site-footer">
  <div class="wrap">
    <nav class="footer-nav">
      <a href="#">Home</a><span class="sep">|</span><a href="#">About Us</a><span class="sep">|</span><a href="#">Services</a><span class="sep">|</span><a href="#">Projects</a><span class="sep">|</span><a href="#">Contact Us</a>
    </nav>
    <p class="copyright">Copyright &copy; 2016 &nbsp;Harlow Mechanical Contractors. &nbsp;All rights reserved.</p>
    <div class="social">
      <span class="one" aria-label="Social profile"></span>
      <span class="two" aria-label="Social profile"></span>
    </div>
  </div>
</footer>

</body>
</html>
```